Barrister at Law needs Business Card Design

Need a business card design for Barrister at Law. Double sided. Simple Neil Thorsby and Barrister at Law on one side with contact details on the other side. I would like a professional design using Black or Platinum. Details on reverse side would include qualifications - Bcom-Llb and Acc Spec Commercial Litigation. I have attached the logo. Contact details would include address/ Po Box/ Phone/Fax/Mobile/email. I would like to use raised print or spot gloss.

```html
<!DOCTYPE html>
<html lang="en">
<head>
<meta charset="utf-8">
<title>Neil Thorsby – Barrister-at-Law Business Card</title>
<link href="https://fonts.googleapis.com/css2?family=Cinzel:wght@400;600&family=Open+Sans:wght@400;600&display=swap" rel="stylesheet">
<style>
  :root {
    --backdrop: #3d3634;
    --card-black: #1b1b1d;
    --card-edge: #111112;
    --blue: #2f8fd6;
    --blue-light: #5cc3f0;
    --blue-deep: #1f6fb2;
    --platinum: #c9cbce;
    --text-light: #e9ecef;
  }
  html, body {
    margin: 0;
    width: 1200px;
    height: 814px;
    overflow: hidden;
    background: var(--backdrop);
  }
  .stage {
    position: relative;
    width: 1200px;
    height: 814px;
  }
  .card {
    position: absolute;
    top: 258px;
    width: 520px;
    height: 297px;
    background: var(--card-black);
    box-shadow: 0 10px 28px rgba(0,0,0,0.45);
    overflow: hidden;
  }
  .card-front { left: 60px; }
  .card-back { left: 620px; }

  .front-identity {
    position: absolute;
    left: 0; right: 0;
    top: 116px;
    text-align: center;
    font-family: 'Cinzel', serif;
  }
  .front-name {
    margin: 0;
    font-size: 26px;
    font-weight: 400;
    color: var(--blue-deep);
    letter-spacing: 1px;
  }
  .front-title {
    margin: 4px 0 0;
    font-size: 19px;
    color: var(--platinum);
    letter-spacing: 0.5px;
  }

  .back-shapes {
    position: absolute;
    inset: 0;
  }
  .contact-list {
    position: absolute;
    left: 22px;
    top: 58px;
    margin: 0;
    padding: 0;
    list-style: none;
    font-family: 'Open Sans', sans-serif;
    font-size: 13px;
    color: var(--text-light);
  }
  .contact-list li {
    display: flex;
    align-items: center;
    gap: 10px;
    height: 21px;
  }
  .contact-icon { width: 12px; height: 12px; flex: none; }
  .address {
    position: absolute;
    right: 22px;
    top: 184px;
    margin: 0;
    text-align: right;
    font-family: 'Open Sans', sans-serif;
    font-style: normal;
    font-size: 14px;
    line-height: 21px;
    color: var(--text-light);
  }
  .website {
    position: absolute;
    right: 26px;
    bottom: 12px;
    margin: 0;
    font-family: 'Open Sans', sans-serif;
    font-size: 15px;
    letter-spacing: 3px;
    color: #ffffff;
  }
</style>
</head>
<body>
<main class="stage">

  <section class="card card-front">
    <div class="front-identity">
      <h1 class="front-name">Neil Thorsby</h1>
      <p class="front-title">Barrister-at-Law</p>
    </div>
  </section>

  <section class="card card-back">
    <svg class="back-shapes" width="520" height="297" viewBox="0 0 520 297">
      <defs>
        <linearGradient id="bandGradient" x1="0" y1="0" x2="1" y2="0">
          <stop offset="0" stop-color="#2a7fcf"/>
          <stop offset="1" stop-color="#1c5f9f"/>
        </linearGradient>
      </defs>
      <line x1="20" y1="168" x2="470" y2="168" stroke="#8a8d92" stroke-width="1"/>
      <polygon points="0,186 248,186 262,200 0,200" fill="#b9bcc0"/>
      <polygon points="0,200 262,200 282,226 520,226 520,297 0,297" fill="var(--blue-light)"/>
      <polygon points="0,210 255,210 275,236 520,236 520,297 0,297" fill="url(#bandGradient)"/>
      <rect x="428" y="0" width="58" height="120" fill="var(--blue-light)"/>
      <circle cx="457" cy="98" r="46" fill="#161618" stroke="#ffffff" stroke-width="3"/>
    </svg>

    <ul class="contact-list">
      <li><svg class="contact-icon" viewBox="0 0 12 12"><path d="M3 1l2 2-1 1.5c.7 1.5 1.8 2.6 3.5 3.5L9 7l2 2-1.5 2C5 11 1 7 1 2.5z" fill="var(--blue)"/></svg>612 555 0147</li>
      <li><svg class="contact-icon" viewBox="0 0 12 12"><rect x="3" y="0.5" width="6" height="11" rx="1" fill="none" stroke="var(--blue)" stroke-width="1.3"/></svg>612 555 0193</li>
      <li><svg class="contact-icon" viewBox="0 0 12 12"><rect x="1" y="4" width="10" height="6" fill="var(--blue)"/><rect x="3" y="1" width="6" height="3" fill="var(--blue)"/></svg>612 555 0128</li>
      <li><svg class="contact-icon" viewBox="0 0 12 12"><rect x="0.5" y="2" width="11" height="8" fill="var(--blue)"/><path d="M0.5 2l5.5 4.5L11.5 2" fill="none" stroke="#1b1b1d" stroke-width="1"/></svg>chambers@thorsbylaw.com</li>
    </ul>

    <address class="address">42 Harbour Street<br>Brisbane, QLD 4000</address>
    <p class="website">www.thorsbylaw.com</p>
  </section>

</main>
</body>
</html>
```